Brell Stone Company Business Cards

Front and Back Business Card - logo and text setup - cool design. I need workable photoshop or illustrator files so I can setup each employee card with design that is created
Updates

Hi everyone, thank you for the great entries. Please no more white and blue cards - there are so many already - black and silver only now please. thanks!

Target Market(s)

Construction Industry - Facility Managers

Industry/Entity Type

Construction

Contact Information for Business Card

I really like contemporary simplistic looks - clean neat....not opposed to seeing some black backrounds

Requirements
Must have
• Logo/website address with design on front only - www.brellstone-example.com (logo attached)
• Back:
• Name/Title/Company Address/Phone/email address
Nice to have
• Cool design
Should not have
• Nothing gimmicky like Fire or Water - since we are a Fire Protection company - it has all been done

```html
<!DOCTYPE html>
<html lang="en">
<head>
<meta charset="utf-8">
<title>Brell Stone Company – Business Cards</title>
<link rel="stylesheet" href="https://fonts.googleapis.com/css2?family=Work+Sans:wght@400;500;800&display=swap">
<style>
  :root {
    --black: #141414;
    --black-soft: #222324;
    --silver: #c4c7cc;
    --silver-light: #e4e6e9;
    --silver-dark: #8d9096;
    --text-grey: #55585d;
    --stage: #3a3b3e;
  }
  * { box-sizing: border-box; margin: 0; padding: 0; }
  html, body {
    width: 1200px; height: 900px; overflow: hidden;
    background: var(--stage);
    font-family: "Work Sans", Arial, sans-serif;
  }
  .canvas {
    width: 1200px; height: 900px;
    display: flex; flex-direction: column;
    align-items: center; justify-content: center; gap: 40px;
  }
  .card {
    width: 700px; height: 400px; position: relative;
    box-shadow: 0 14px 30px rgba(0,0,0,.45);
  }

  /* Back: contact side, silver stock */
  .card-back {
    background: linear-gradient(135deg, var(--silver) 0%, var(--silver-light) 50%, #f1f2f4 100%);
  }
  .name-marker {
    position: absolute; left: 0; top: 40px;
    width: 18px; height: 34px; background: var(--black);
  }
  .person-name {
    position: absolute; left: 36px; top: 38px;
    color: var(--black); font-weight: 500; font-size: 26px; letter-spacing: 1.5px;
  }
  .person-title {
    position: absolute; left: 36px; top: 72px;
    color: var(--text-grey); font-size: 15px; letter-spacing: .5px;
  }
  .divider {
    position: absolute; left: 36px; right: 60px; top: 200px;
    height: 2px; background: var(--black);
  }
  .address {
    position: absolute; left: 36px; top: 222px;
    color: var(--text-grey); font-size: 15px; line-height: 1.55; letter-spacing: .4px;
  }
  .brand-name {
    position: absolute; right: 60px; top: 128px;
    display: flex; align-items: center; gap: 12px;
  }
  .brand-name .brand-square { width: 20px; height: 20px; background: var(--silver-dark); }
  .card-back .brand-name .word {
    color: var(--black); font-weight: 800; font-size: 44px; letter-spacing: -.5px;
  }
  .contacts {
    position: absolute; right: 60px; bottom: 36px;
    list-style: none;
    color: var(--text-grey); font-size: 15px; line-height: 1.7; letter-spacing: .4px;
  }
  .contacts li { display: flex; justify-content: flex-end; align-items: center; gap: 10px; }
  .contacts svg { width: 12px; height: 12px; fill: var(--black); }

  /* Front: brand side, black stock */
  .card-front {
    background: linear-gradient(160deg, var(--black-soft) 0%, var(--black) 100%);
    display: flex; flex-direction: column; align-items: center; justify-content: center; gap: 18px;
  }
  .card-front .brand-name { position: static; gap: 16px; }
  .card-front .brand-name .brand-square { width: 26px; height: 26px; background: var(--silver-dark); }
  .card-front .brand-name .word {
    color: var(--silver); font-weight: 800; font-size: 58px; letter-spacing: -1px;
  }
  .front-web { color: var(--silver); font-size: 16px; letter-spacing: 1px; }
</style>
</head>
<body>
<main class="canvas">

  <section class="card card-back" aria-label="Card back with contact details">
    <div class="name-marker"></div>
    <h1 class="person-name">DANIEL HARPER</h1>
    <p class="person-title">Director</p>

    <div class="brand-name">
      <span class="word">Brell Stone</span>
      <span class="brand-square"></span>
    </div>

    <div class="divider"></div>
    <p class="address">48 Meridian Way<br>Lakeport, NY 10500</p>

    <ul class="contacts">
      <li>(555) 014-2231
        <svg viewBox="0 0 24 24" aria-hidden="true"><path d="M6.6 10.8a15 15 0 0 0 6.6 6.6l2.2-2.2a1 1 0 0 1 1-.25 11.4 11.4 0 0 0 3.6.57 1 1 0 0 1 1 1V20a1 1 0 0 1-1 1A17 17 0 0 1 3 4a1 1 0 0 1 1-1h3.5a1 1 0 0 1 1 1c0 1.25.2 2.45.57 3.57a1 1 0 0 1-.25 1z"/></svg>
      </li>
      <li>(555) 014-2232
        <svg viewBox="0 0 24 24" aria-hidden="true"><path d="M6 3h9v5H6zM4 9h16a2 2 0 0 1 2 2v7h-4v3H6v-3H2v-7a2 2 0 0 1 2-2zm4 7v3h8v-3z"/></svg>
      </li>
      <li>info@brellstone-example.com
        <svg viewBox="0 0 24 24" aria-hidden="true"><path d="M2 5h20v14H2zm2 2v.5l8 5 8-5V7zm0 2.8V17h16V9.8l-8 5z"/></svg>
      </li>
      <li>www.brellstone-example.com
        <svg viewBox="0 0 24 24" aria-hidden="true"><path d="M12 2a10 10 0 1 0 0 20 10 10 0 0 0 0-20zm0 2c.9 1.2 1.6 2.6 2 4h-4c.4-1.4 1.1-2.8 2-4zM4.3 14a8 8 0 0 1 0-4h3.4a16 16 0 0 0 0 4zm.8 2h3c.3 1.3.8 2.5 1.5 3.6A8 8 0 0 1 5.1 16zM8 8H5.1a8 8 0 0 1 4.5-3.6C8.9 5.5 8.4 6.7 8 8zm4 12c-.9-1.2-1.6-2.6-2-4h4c-.4 1.4-1.1 2.8-2 4zm2.3-6H9.7a14 14 0 0 1 0-4h4.6a14 14 0 0 1 0 4zm.1 5.6c.7-1.1 1.2-2.3 1.5-3.6h3a8 8 0 0 1-4.5 3.6zM16.3 14a16 16 0 0 0 0-4h3.4a8 8 0 0 1 0 4z"/></svg>
      </li>
    </ul>
  </section>

  <section class="card card-front" aria-label="Card front with company name">
    <div class="brand-name">
      <span class="word">Brell Stone</span>
      <span class="brand-square"></span>
    </div>
    <p class="front-web">www.brellstone-example.com</p>
  </section>

</main>
</body>
</html>
```